HVAC Company Business Card design with attached logo

Looking for an easily readable and attractive business card design that includes my attached company logo. I selected one sided card because it's more traditional, but I'm open to a 2-sided design. All of the details should be included in the design. Looking to create a professional, upscale image.

Target Market(s)

Commercial and residential consumers

Industry/Entity Type

Hvac

Contact Information for Business Card

Company phone number is 631.487.2953
Company email marcus@tidewellhvac.example
Company name is Bright Harbor Air Conditioning, Refrigeration, and Heating
Marcus Delgado
Owner Operator
Company Address is
PO Box 872,
712 Fenwyck Ln,
Elmsport, VT 11752
Business License K8195240000
Insured

Font styles to use
Serif
Sans Serif

Colors

Designer to choose colors to be used in the design.

Requirements
Must have
• Must include the logo.
Nice to have
• It seems like it should be a one sided card, but I'm open to a 2 sided one.

```html
<!DOCTYPE html>
<html lang="en">
<head>
<meta charset="utf-8">
<title>Bright Harbor HVAC – Business Card</title>
<link href="https://fonts.googleapis.com/css2?family=Roboto:wght@300;400;500;700;900&display=swap" rel="stylesheet">
<style>
  :root {
    --stage: #2a2a2c;
    --card: #2b2b2d;
    --card-edge: #232325;
    --blue: #3a5bb8;
    --orange: #f2692a;
    --ink: #e6e6e6;
    --muted: #cfcfcf;
  }
  * { box-sizing: border-box; margin: 0; padding: 0; }
  html, body {
    width: 1200px; height: 1000px; overflow: hidden;
    background: var(--stage);
    font-family: "Roboto", Arial, sans-serif;
  }
  .card {
    position: absolute; left: 230px; width: 740px; height: 430px;
    background: var(--card);
    border: 1px solid var(--card-edge);
    box-shadow: 0 10px 30px rgba(0,0,0,.45);
    display: flex; flex-direction: column; align-items: center;
  }
  .card--front { top: 50px; justify-content: center; }
  .card--back { top: 520px; padding-top: 30px; }

  .brand { display: flex; flex-direction: column; align-items: center; }
  .brand__row { display: flex; align-items: center; gap: 16px; }
  .brand__dot { width: 46px; height: 46px; border-radius: 50%; background: var(--orange); }
  .brand__name {
    font-weight: 900; color: var(--blue); font-size: 52px;
    letter-spacing: -1px; line-height: 1; text-transform: uppercase;
  }
  .brand__tagline {
    margin-top: 8px; color: #fff; font-weight: 500;
    font-size: 14px; letter-spacing: 2.5px; text-transform: uppercase;
  }
  .card--back .brand__dot { width: 36px; height: 36px; }
  .card--back .brand__name { font-size: 40px; }
  .card--back .brand__tagline { font-size: 11.5px; letter-spacing: 2px; margin-top: 6px; }

  .website { margin-top: 80px; color: var(--muted); font-size: 20px; font-weight: 300; letter-spacing: 1.5px; }
  .website b, .accent { color: var(--orange); font-weight: 400; }

  .person__name {
    margin-top: 18px; color: var(--blue); font-weight: 900;
    font-size: 30px; text-transform: uppercase; letter-spacing: .5px; text-align: center;
  }
  .person__role { color: var(--orange); font-weight: 500; font-size: 17px; text-align: center; }

  .icons { display: flex; gap: 14px; margin-top: 14px; }
  .icon { width: 40px; height: 40px; }

  .contact {
    margin-top: 12px; text-align: center; color: var(--ink);
    font-weight: 300; font-size: 19px; line-height: 1.28; letter-spacing: 1px;
  }
  .contact .label { color: var(--orange); font-weight: 500; }
  .contact .license { margin-top: 6px; }
</style>
</head>
<body>
  <section class="card card--front">
    <div class="brand">
      <div class="brand__row">
        <span class="brand__dot"></span>
        <span class="brand__name">Bright Harbor</span>
      </div>
      <span class="brand__tagline">Air Conditioning, Refrigeration and Heating</span>
    </div>
    <p class="website">www.<b>tidewellhvac</b>.example</p>
  </section>

  <section class="card card--back">
    <div class="brand">
      <div class="brand__row">
        <span class="brand__dot"></span>
        <span class="brand__name">Bright Harbor</span>
      </div>
      <span class="brand__tagline">Air Conditioning, Refrigeration and Heating</span>
    </div>

    <h1 class="person__name">Marcus Delgado</h1>
    <p class="person__role">Owner Operator</p>

    <div class="icons">
      <svg class="icon" viewBox="0 0 40 40" aria-label="Phone">
        <circle cx="20" cy="20" r="18" fill="none" stroke="var(--blue)" stroke-width="2"/>
        <path d="M15 12c1 0 2 3 2 4s-1.5 1.5-1.2 2.5c.8 2 2.2 3.4 4.2 4.2 1 .3 1.5-1.2 2.5-1.2s4 1 4 2-1.5 3-3 3C18 26.5 13.5 22 13.5 15c0-1.5 .5-3 1.5-3z" fill="var(--orange)"/>
      </svg>
      <svg class="icon" viewBox="0 0 40 40" aria-label="Email">
        <circle cx="20" cy="20" r="18" fill="none" stroke="var(--blue)" stroke-width="2"/>
        <rect x="11" y="14" width="18" height="12" fill="var(--orange)"/>
        <path d="M11 14l9 7 9-7" fill="none" stroke="var(--card)" stroke-width="1.5"/>
      </svg>
      <svg class="icon" viewBox="0 0 40 40" aria-label="Website">
        <circle cx="20" cy="20" r="18" fill="none" stroke="var(--blue)" stroke-width="2"/>
        <g fill="none" stroke="var(--orange)" stroke-width="1.5">
          <circle cx="20" cy="20" r="8"/>
          <ellipse cx="20" cy="20" rx="3.5" ry="8"/>
          <path d="M12 20h16M13.5 16h13M13.5 24h13"/>
        </g>
      </svg>
    </div>

    <div class="contact">
      <p>631.487.2953</p>
      <p>marcus@tidewellhvac.example</p>
      <p>www.<span class="accent">tidewellhvac</span>.example</p>
      <p class="license"><span class="label">License:</span> K8195240000</p>
      <p>PO Box 872, 712 Fenwyck Ln, Elmsport, VT 11752</p>
    </div>
  </section>
</body>
</html>
```